wealth management firm, professional group, new model

we have a logo that works but we need a card, white background using our colors...clean look

our tag line if can be used in

Building Lasting Value Together

```html
<!DOCTYPE html>
<html lang="en">
<head>
<meta charset="utf-8">
<title>Larkmoor Advisory – Business Card</title>
<link href="https://fonts.googleapis.com/css2?family=Montserrat:wght@400;500;700&display=swap" rel="stylesheet">
<style>
  :root {
    --backdrop: #8a8a8a;
    --card: #f7f7f8;
    --navy: #1b2a4e;
  }
  * { box-sizing: border-box; margin: 0; padding: 0; }
  html, body { width: 1200px; height: 1050px; overflow: hidden; }
  body {
    background: var(--backdrop);
    font-family: "Montserrat", sans-serif;
    color: var(--navy);
    display: flex;
    flex-direction: column;
    align-items: center;
    justify-content: center;
    gap: 70px;
  }
  .card {
    width: 700px;
    height: 400px;
    background: var(--card);
    position: relative;
    box-shadow: 0 14px 30px rgba(0,0,0,0.25);
  }
  .card--front { border-bottom: 6px solid var(--navy); }

  .wordmark {
    font-weight: 500;
    color: var(--navy);
    white-space: nowrap;
    line-height: 1;
  }
  .card--front .wordmark {
    position: absolute; top: 120px; left: 0; right: 0;
    text-align: center; font-size: 46px; letter-spacing: 0.02em;
  }
  .card--back .wordmark {
    position: absolute; top: 180px; right: 50px;
    font-size: 30px; letter-spacing: 0.02em;
  }

  .tagline-row {
    position: absolute;
    left: 0; right: 30px; top: 262px;
    display: flex; align-items: center; gap: 12px;
  }
  .tagline-row .rule { flex: 1; height: 1.5px; background: var(--navy); }
  .tagline { font-size: 17px; font-weight: 500; letter-spacing: 0.05em; white-space: nowrap; }

  .contact { position: absolute; left: 50px; top: 105px; font-size: 16px; line-height: 1.55; }
  .contact__name { font-size: 25px; font-weight: 700; letter-spacing: 0.01em; line-height: 1.1; }
  .contact__role { font-size: 18px; margin-bottom: 8px; }
  .contact__line { display: flex; align-items: center; gap: 8px; }
  .contact__line svg { width: 14px; height: 14px; flex: none; }
  .contact__phone { letter-spacing: 0.12em; }
</style>
</head>
<body>

  <section class="card card--front">
    <p class="wordmark">Larkmoor Advisory</p>
    <div class="tagline-row">
      <span class="rule"></span>
      <span class="tagline">Building Lasting Value Together</span>
      <span class="rule"></span>
    </div>
  </section>

  <section class="card card--back">
    <div class="contact">
      <p class="contact__name">DANIEL HARTLEY</p>
      <p class="contact__role">Advisor</p>
      <p>480 Linden Row</p>
      <p>Maple Harbor, FL 32000</p>
      <p class="contact__line contact__phone">
        <svg viewBox="0 0 16 16" aria-hidden="true"><path fill="var(--navy)" d="M3.6 1.2l2.2 2.6-1.3 1.6c.9 2 2.3 3.4 4.2 4.3l1.6-1.3 2.6 2.2-1.2 2.2C6.6 12.5 3.4 9.3 1.4 2.4z"/></svg>
        555-014-2286
      </p>
      <p class="contact__line">
        <svg viewBox="0 0 16 16" aria-hidden="true"><rect x="1" y="3" width="14" height="10" fill="var(--navy)"/><path d="M1.5 3.5L8 9l6.5-5.5" stroke="var(--card)" stroke-width="1.3" fill="none"/></svg>
        hello@larkmoor.com
      </p>
      <p class="contact__line">
        <svg viewBox="0 0 16 16" aria-hidden="true"><g fill="none" stroke="var(--navy)" stroke-width="1.3"><circle cx="8" cy="8" r="6.5"/><ellipse cx="8" cy="8" rx="3" ry="6.5"/><path d="M1.5 8h13M2.5 4.8h11M2.5 11.2h11"/></g></svg>
        larkmoor.com
      </p>
    </div>
    <p class="wordmark">Larkmoor Advisory</p>
  </section>

</body>
</html>
```